Brindle Asset Management Vendor Recruiting Email

We need a digital flyer to email and post on Social media to attract new vendors to our website to apply to complete maintenance work on our clients homes. I have one flyer we had produced recently that we are un-happy with. It is attached.

The example given is what we do not want!! We do not want any of the pictures used from the existing one

Target Market(s)

Construction companies and handyman

Industry/Entity Type

Residential maintenance and repairs

Requirements
Must have
• Join our team as the header not become a vendor

```html
<!DOCTYPE html>
<html lang="en">
<head>
<meta charset="utf-8">
<title>Brindle Asset Management – Join Our Team</title>
<link rel="stylesheet" href="https://fonts.googleapis.com/css2?family=Great+Vibes&family=Montserrat:wght@700&family=Lexend:wght@500;700;800&family=Roboto+Condensed:wght@300;700&display=swap">
<style>
  :root {
    --frame-purple: #684d80;
    --brand-purple: #6a2b93;
    --brand-purple-light: #8a3fb8;
    --ink: #1d1b26;
    --white: #ffffff;
    --panel-white: rgba(255,255,255,0.78);
    --logo-black: #0c0a14;
  }
  * { margin: 0; padding: 0; box-sizing: border-box; }
  html, body { width: 1200px; height: 897px; overflow: hidden; background: var(--frame-purple); }
  .flyer { position: relative; width: 1200px; height: 897px; background: var(--frame-purple); font-family: "Lexend", sans-serif; color: var(--ink); }

  .hero-frame {
    position: absolute; left: 41px; top: 37px; width: 1118px; height: 794px;
    border: 4px solid var(--white); border-radius: 32px; overflow: hidden;
  }
  .hero-photo {
    position: absolute; inset: 0;
    background:
      linear-gradient(90deg, rgba(40,50,90,0.55) 0%, rgba(40,50,90,0.15) 35%, rgba(0,0,0,0) 55%),
      linear-gradient(180deg, #9cc3ea 0%, #c9def2 38%, #d9e2e6 55%, #a8b59a 72%, #5f9a3a 86%, #4f8a2c 100%);
  }

  .title { position: absolute; right: 34px; text-align: right; white-space: nowrap; }
  .title-script { top: 92px; font-family: "Great Vibes", cursive; font-size: 86px; line-height: 1; color: #111; }
  .title-main {
    top: 192px; font-family: "Montserrat", sans-serif; font-weight: 700; font-size: 90px; line-height: 1;
    letter-spacing: 1px;
    background: linear-gradient(180deg, var(--brand-purple-light), var(--brand-purple));
    -webkit-background-clip: text; background-clip: text; color: transparent;
  }

  .benefits-panel {
    position: absolute; left: 69px; top: 292px; width: 523px; height: 455px;
    background: var(--panel-white); border-radius: 4px 4px 18px 4px;
  }
  .bullet-list { list-style: none; }
  .bullet-list li { position: relative; font-weight: 500; line-height: 24px; }
  .bullet-list li::before {
    content: ""; position: absolute; left: -29px; top: 7px; width: 10px; height: 10px;
    border-radius: 50%; background: var(--brand-purple);
  }
  .benefits { position: absolute; left: 66px; top: 58px; width: 440px; font-size: 23px; letter-spacing: 0.2px; }
  .benefits li { margin-bottom: 24px; }

  .contact { position: absolute; left: 66px; top: 346px; }
  .contact-icon { position: absolute; left: 0; top: 0; width: 56px; height: 76px; }
  .contact-label { position: absolute; left: 71px; top: -6px; white-space: nowrap; font-family: "Roboto Condensed", sans-serif; font-weight: 300; font-size: 34px; color: var(--brand-purple); }
  .contact-phone { position: absolute; left: 70px; top: 28px; white-space: nowrap; font-family: "Roboto Condensed", sans-serif; font-weight: 700; font-size: 58px; line-height: 1; letter-spacing: -1px; color: var(--brand-purple); }

  .requirements { position: absolute; left: 686px; top: 345px; width: 335px; }
  .requirements-heading { font-weight: 800; font-size: 29px; line-height: 38px; color: var(--ink); text-transform: uppercase; letter-spacing: -0.8px; }
  .requirements-list { margin-top: 18px; font-size: 21px; letter-spacing: 0.2px; }
  .requirements-list li { margin-bottom: 15px; }
  .requirements-list li::before { left: -35px; }

  .logo-block {
    position: absolute; left: 800px; top: 753px; width: 237px; height: 131px;
    background: var(--logo-black); display: flex; flex-direction: column; align-items: center; justify-content: center; gap: 8px;
    color: var(--white); font-weight: 700; text-align: center;
  }
  .logo-mark { width: 30px; height: 30px; border-radius: 50%; background: var(--brand-purple-light); }
  .logo-name { font-size: 20px; letter-spacing: 2px; line-height: 1; }
  .logo-sub { font-size: 9px; letter-spacing: 1.5px; line-height: 1; }

  .website { position: absolute; left: 137px; top: 845px; display: flex; align-items: center; gap: 13px; }
  .website-text { font-family: "Lexend", sans-serif; font-weight: 700; font-style: italic; font-size: 31px; line-height: 1; color: var(--white); }
</style>
</head>
<body>
<div class="flyer">
  <div class="hero-frame">
    <div class="hero-photo" role="img" aria-label="Photo of a tradesman in navy overalls with a tool belt writing on a clipboard, in front of a blurred house and green lawn under a blue sky"></div>

    <div class="title title-script">Join</div>
    <div class="title title-main">OUR TEAM</div>

    <div class="benefits-panel">
      <ul class="bullet-list benefits">
        <li>95% approval rating on all submitted climates.</li>
        <li>Guaranteed work volume.</li>
        <li>Material purchasing program to help vendors</li>
        <li>Weekly secure direct deposit with net 30 payment terms</li>
      </ul>
      <div class="contact">
        <svg class="contact-icon" viewBox="0 0 56 76" aria-hidden="true">
          <rect x="0" y="0" width="56" height="76" rx="4" fill="#6a2b93"/>
          <rect x="44" y="4" width="8" height="68" fill="#fff"/>
          <rect x="47" y="8" width="2" height="60" fill="#6a2b93"/>
          <path d="M13 20c-3 3-3 9 2 18s11 14 15 15c3 1 6-1 7-3l-6-7-4 2c-3-2-7-8-8-11l3-3-4-8z" fill="#fff"/>
        </svg>
        <div class="contact-label">More information call us</div>
        <div class="contact-phone">734-555-0187</div>
      </div>
    </div>

    <div class="requirements">
      <h2 class="requirements-heading">Requirements to<br>become a vendor</h2>
      <ul class="bullet-list requirements-list">
        <li>Auto insurance</li>
        <li>Certificate of general liability insurance</li>
        <li>Workman’s Compensation or state issued exemption letter</li>
        <li>Coverage area</li>
        <li>Any speciality Licenses</li>
      </ul>
    </div>
  </div>

  <div class="logo-block">
    <div class="logo-mark"></div>
    <div class="logo-name">BRINDLE</div>
    <div class="logo-sub">ASSET MANAGEMENT</div>
  </div>

  <div class="website">
    <svg width="31" height="31" viewBox="0 0 32 32" aria-hidden="true" fill="none" stroke="#fff" stroke-width="2">
      <circle cx="16" cy="16" r="14"/>
      <ellipse cx="16" cy="16" rx="6" ry="14"/>
      <line x1="2" y1="16" x2="30" y2="16"/>
    </svg>
    <span class="website-text">www.brindleassetmgmt.com</span>
  </div>
</div>
</body>
</html>
```